Zenqo - revolutionary mobile payment

The app is a P2P money trasfert, without the using of credit card or bank circuits it can transfer electronic money from one person to another consumers simply and immediatelly.
You can use the color you want, but the message we need to transert to consumer is simplicity, safety and coolness.
In attach the logo of the company and the wireframe of thre page of the app.
The goal is to design the page of the app with a clear, simple and intuitive graphic.
Updates

I have upgrade the brief with important information and detail, many thanks

Target Market(s)

all the people

Industry/Entity Type

Credit Card

Requirements
Must have
• You have to design one icon for each button in the first page, (shop is: where to shop)
in the second one a new intuitive image (instead of the hand) that let the user to understand that with a simple swipe he can process the payment
Nice to have
• You can include or esxclude what you want or belive can improve user experience of the app
Should not have
• too much color, too much button or information

```html
<!DOCTYPE html>
<html lang="it">
<head>
<meta charset="utf-8">
<title>Zenqo – mobile payment screens</title>
<link href="https://fonts.googleapis.com/css2?family=Mulish:wght@400;600;700;800&display=swap" rel="stylesheet">
<style>
  :root {
    --page: #eeeef3;
    --status: #0b0b0b;
    --toolbar: #e9e9ec;
    --header: #56648c;
    --header-dark: #46547c;
    --tile: rgba(36, 50, 98, 0.88);
    --tile-line: rgba(255, 255, 255, 0.55);
    --key: rgba(48, 62, 110, 0.9);
    --key-accent: #e8601c;
    --row: #33457c;
    --row-icon: #25366a;
    --brand: #1f4aa6;
    --ink: #222;
    --white: #fff;
    --danger: #c4262b;
    --go: #279a3e;
    --amount-bg: #b7b7ba;
  }
  * { box-sizing: border-box; margin: 0; padding: 0; }
  html, body { width: 1200px; height: 866px; overflow: hidden; }
  body { background: var(--page); font-family: "Mulish", sans-serif; color: var(--ink); position: relative; }

  .screen { position: absolute; top: 194px; width: 270px; height: 480px; overflow: hidden; background: #ddd; }
  .screen--home { left: 100px; }
  .screen--pay { left: 467px; }
  .screen--balance { left: 828px; }

  .backdrop { position: absolute; left: 0; right: 0; top: 54px; bottom: 0;
    background: linear-gradient(100deg, #f2f2f2 0%, #c9c9cc 18%, #5a5a60 35%, #d9d9dc 52%, #9a4a52 72%, #e3e3e6 88%, #f0f0f0 100%); }

  .status-bar { position: absolute; top: 0; left: 0; right: 0; height: 22px; background: var(--status); color: var(--white);
    font-size: 9px; font-weight: 600; display: flex; align-items: center; justify-content: space-between; padding: 0 6px; }
  .status-bar .carrier, .status-bar .battery { display: flex; align-items: center; gap: 3px; }
  .status-bar .time { font-size: 10px; }

  .toolbar { position: absolute; top: 22px; left: 0; right: 0; height: 32px; background: linear-gradient(#f6f6f7, var(--toolbar));
    display: flex; align-items: center; justify-content: space-between; padding: 0 8px; }
  .brand { display: flex; align-items: center; gap: 4px; color: var(--brand); font-weight: 800; font-size: 12px; }
  .brand-dot { width: 14px; height: 14px; border: 2px solid var(--brand); border-radius: 50%; }

  .header { position: absolute; top: 54px; left: 0; right: 0; background: var(--header); color: var(--white); }
  .header--profile, .header--balance { height: 94px; }
  .header--pay { height: 59px; }
  .avatar { position: absolute; width: 62px; height: 62px; border-radius: 50%; border: 3px solid var(--white);
    background: radial-gradient(circle at 50% 40%, #c9a58a 0 30%, #5d6f4e 60%, #3e4a37 100%); }
  .header--profile .avatar { left: 10px; top: 16px; }
  .profile-name { position: absolute; left: 80px; top: 30px; font-size: 15px; font-weight: 700; }
  .profile-phone { position: absolute; left: 80px; top: 50px; font-size: 8.5px; opacity: .85; }
  .edit-btn { position: absolute; right: 12px; top: 36px; width: 20px; height: 20px; border-radius: 50%; background: var(--white);
    display: flex; align-items: center; justify-content: center; }

  .back-link { position: absolute; left: 6px; font-size: 10px; color: var(--white); }
  .header--pay .back-link { top: 24px; }
  .pay-title { position: absolute; left: 0; right: 0; top: 14px; display: flex; justify-content: center; align-items: center; gap: 6px;
    font-size: 19px; font-weight: 700; }

  .header--balance .back-block { position: absolute; left: 0; top: 0; width: 55px; height: 94px; background: var(--header-dark); }
  .header--balance .back-link { top: 40px; }
  .balance-label { position: absolute; right: 84px; top: 30px; font-size: 10px; font-weight: 700; text-align: right; }
  .balance-value { position: absolute; right: 84px; top: 44px; font-size: 17px; font-weight: 800; }
  .header--balance .avatar { right: 10px; top: 16px; }

  .tiles { position: absolute; left: 20px; top: 195px; display: grid; grid-template-columns: 104px 104px; gap: 21px 19px; }
  .tile { height: 104px; background: var(--tile); color: var(--white); display: flex; flex-direction: column; align-items: center;
    justify-content: center; gap: 6px; font-size: 11px; font-weight: 700; }

  .phone-field { position: absolute; left: 36px; top: 141px; width: 197px; height: 33px; background: var(--white); border: 1px solid #bbb;
    display: flex; align-items: center; font-size: 10px; }
  .phone-field .icon { width: 26px; height: 100%; display: flex; align-items: center; justify-content: center; border-right: 1px solid #ccc; }
  .phone-field .prefix { font-weight: 800; margin: 0 5px 0 6px; }
  .amount { position: absolute; left: 6px; top: 195px; width: 250px; height: 48px; display: flex; align-items: center; }
  .amount .currency { width: 35px; font-size: 24px; color: #555; text-align: center; }
  .amount .value { flex: 1; height: 100%; background: var(--amount-bg); display: flex; align-items: center; justify-content: center;
    font-size: 23px; font-weight: 800; color: #151515; }
  .note-toggle { position: absolute; left: 10px; top: 264px; font-size: 7px; color: var(--ink); }

  .keypad { position: absolute; left: 6px; top: 277px; width: 258px; height: 199px; display: grid; grid-template-columns: repeat(3, 1fr);
    grid-template-rows: repeat(4, 1fr); gap: 2px; }
  .key { background: var(--key); color: var(--white); display: flex; align-items: center; justify-content: center; font-size: 19px; font-weight: 600; }
  .key--active { background: var(--key-accent); }

  .range-select { position: absolute; left: 188px; top: 153px; width: 76px; height: 15px; background: var(--row); color: var(--white);
    font-size: 6.5px; display: flex; align-items: center; justify-content: space-between; padding: 0 5px; }
  .transactions { position: absolute; left: 33px; top: 182px; width: 199px; list-style: none; display: flex; flex-direction: column; gap: 7px; }
  .transaction { height: 26px; background: var(--row); color: var(--white); display: flex; align-items: center; font-size: 8.5px; }
  .transaction .kind { width: 24px; height: 100%; background: var(--row-icon); display: flex; align-items: center; justify-content: center; }
  .transaction .number { margin-left: 7px; width: 100px; }
  .transaction .sum { width: 48px; font-weight: 700; }
  .transaction .more { margin-left: auto; margin-right: 6px; }

  .actions { position: absolute; left: 30px; top: 425px; display: flex; gap: 15px; }
  .action { width: 95px; height: 39px; display: flex; align-items: center; justify-content: center; color: var(--white); font-size: 11px; font-weight: 700; }
  .action--report { background: var(--danger); }
  .action--pockets { background: var(--go); }
</style>
</head>
<body>

<!-- Home -->
<section class="screen screen--home">
  <div class="backdrop" role="img" aria-label="Soft blurred lifestyle photo backdrop"></div>
  <div class="status-bar">
    <span class="carrier">●●●○○ NOVA
      <svg width="10" height="8" viewBox="0 0 10 8"><path d="M1 3a6 6 0 0 1 8 0M2.5 4.5a4 4 0 0 1 5 0M5 7l1-1a1.4 1.4 0 0 0-2 0z" fill="none" stroke="#fff" stroke-width="1.1"/></svg></span>
    <span class="time">4:21 PM</span>
    <span class="battery">22% <svg width="20" height="9" viewBox="0 0 20 9"><rect x=".5" y=".5" width="17" height="8" fill="none" stroke="#fff"/><rect x="2" y="2" width="4" height="5" fill="#fff"/><rect x="18" y="3" width="1.5" height="3" fill="#fff"/></svg></span>
  </div>
  <div class="toolbar">
    <svg class="gear" width="18" height="18" viewBox="0 0 18 18"><circle cx="7" cy="10" r="4.5" fill="none" stroke="#333" stroke-width="3" stroke-dasharray="2 1.5"/><circle cx="14" cy="4" r="2.5" fill="none" stroke="#333" stroke-width="1.8"/></svg>
    <span class="brand"><span class="brand-dot"></span>Zenqo</span>
  </div>
  <header class="header header--profile">
    <div class="avatar" role="img" aria-label="User profile photo"></div>
    <div class="profile-name">Marlo Benning</div>
    <div class="profile-phone">+39 300 718 4402</div>
    <div class="edit-btn"><svg width="10" height="10" viewBox="0 0 10 10"><path d="M1 9l1-3 5-5 2 2-5 5z" fill="#333"/></svg></div>
  </header>
  <nav class="tiles">
    <div class="tile">
      <svg width="54" height="44" viewBox="0 0 54 44"><rect x="14" y="14" width="36" height="24" rx="2" fill="#fff"/><rect x="14" y="19" width="36" height="4" fill="#243262"/><path d="M4 2l14 14 6 0 2 6-8 2-16-12z" fill="#fff"/><text x="38" y="34" font-size="10" font-weight="700" fill="#243262" font-family="Mulish, sans-serif">€</text></svg>
      Pay
    </div>
    <div class="tile">
      <svg width="50" height="44" viewBox="0 0 50 44"><path d="M20 0h10v12h7L25 24 13 12h7z" fill="#fff"/><path d="M2 22h12l5 8h12l5-8h12v20H2z" fill="#fff"/><circle cx="38" cy="33" r="7" fill="#243262"/><text x="34.5" y="37" font-size="10" font-weight="700" fill="#fff" font-family="Mulish, sans-serif">€</text></svg>
      Ask
    </div>
    <div class="tile">
      <svg width="44" height="46" viewBox="0 0 44 46"><circle cx="22" cy="11" r="10" fill="#fff"/><path d="M4 46V32c0-6 6-10 12-10h12c6 0 12 4 12 10v14z" fill="#fff"/><path d="M19 23h6l-1 4 2 12-4 4-4-4 2-12z" fill="#243262"/></svg>
      Account
    </div>
    <div class="tile">
      <svg width="50" height="46" viewBox="0 0 50 46"><path d="M2 8l14-6 16 6 16-6v36l-16 6-16-6-14 6z" fill="#fff"/><path d="M25 6a8 8 0 0 1 8 8c0 6-8 16-8 16s-8-10-8-16a8 8 0 0 1 8-8z" fill="#243262"/><circle cx="25" cy="14" r="3" fill="#fff"/></svg>
      Shop
    </div>
  </nav>
</section>

<!-- Pay -->
<section class="screen screen--pay">
  <div class="backdrop" role="img" aria-label="Soft blurred lifestyle photo backdrop"></div>
  <div class="status-bar">
    <span class="carrier">●●●○○ NOVA
      <svg width="10" height="8" viewBox="0 0 10 8"><path d="M1 3a6 6 0 0 1 8 0M2.5 4.5a4 4 0 0 1 5 0M5 7l1-1a1.4 1.4 0 0 0-2 0z" fill="none" stroke="#fff" stroke-width="1.1"/></svg></span>
    <span class="time">4:21 PM</span>
    <span class="battery">22% <svg width="20" height="9" viewBox="0 0 20 9"><rect x=".5" y=".5" width="17" height="8" fill="none" stroke="#fff"/><rect x="2" y="2" width="4" height="5" fill="#fff"/><rect x="18" y="3" width="1.5" height="3" fill="#fff"/></svg></span>
  </div>
  <div class="toolbar">
    <svg class="gear" width="18" height="18" viewBox="0 0 18 18"><circle cx="7" cy="10" r="4.5" fill="none" stroke="#333" stroke-width="3" stroke-dasharray="2 1.5"/><circle cx="14" cy="4" r="2.5" fill="none" stroke="#333" stroke-width="1.8"/></svg>
    <span class="brand"><span class="brand-dot"></span>Zenqo</span>
  </div>
  <header class="header header--pay">
    <span class="back-link">‹ Indietro</span>
    <div class="pay-title">
      <svg width="24" height="26" viewBox="0 0 24 26"><path d="M2 6a6 6 0 0 1 12 0" fill="none" stroke="#fff" stroke-width="2"/><path d="M6 8l4 0M2 4l-2 2 2 2" fill="none" stroke="#fff" stroke-width="1.6"/><path d="M9 10v10l-3-3-2 2 6 7h10l2-9-8-2v-5a2.5 2.5 0 0 0-5 0z" fill="#fff"/></svg>
      Pay
    </div>
  </header>
  <div class="phone-field">
    <span class="icon"><svg width="12" height="18" viewBox="0 0 12 18"><rect x="1" y="1" width="10" height="16" rx="2" fill="none" stroke="#222" stroke-width="1.6"/><rect x="3" y="3.5" width="6" height="10" fill="#222"/></svg></span>
    <span class="prefix">+39</span>Cellulare
  </div>
  <div class="amount"><span class="currency">€</span><span class="value">851.33</span></div>
  <div class="note-toggle">Inserisci note (opzionale) ▾</div>
  <div class="keypad">
    <span class="key">1</span><span class="key">2</span><span class="key">3</span>
    <span class="key">4</span><span class="key">5</span><span class="key">6</span>
    <span class="key">7</span><span class="key key--active">8</span><span class="key">9</span>
    <span class="key">.</span><span class="key">0</span>
    <span class="key"><svg width="20" height="12" viewBox="0 0 20 12"><path d="M6 0h14v12H6L0 6z" fill="#fff"/><path d="M10 3l6 6M16 3l-6 6" stroke="#2f3e6e" stroke-width="1.8"/></svg></span>
  </div>
</section>

<!-- Balance -->
<section class="screen screen--balance">
  <div class="backdrop" role="img" aria-label="Soft blurred lifestyle photo backdrop"></div>
  <div class="status-bar">
    <span class="carrier">●●●○○ NOVA
      <svg width="10" height="8" viewBox="0 0 10 8"><path d="M1 3a6 6 0 0 1 8 0M2.5 4.5a4 4 0 0 1 5 0M5 7l1-1a1.4 1.4 0 0 0-2 0z" fill="none" stroke="#fff" stroke-width="1.1"/></svg></span>
    <span class="time">4:21 PM</span>
    <span class="battery">22% <svg width="20" height="9" viewBox="0 0 20 9"><rect x=".5" y=".5" width="17" height="8" fill="none" stroke="#fff"/><rect x="2" y="2" width="4" height="5" fill="#fff"/><rect x="18" y="3" width="1.5" height="3" fill="#fff"/></svg></span>
  </div>
  <div class="toolbar">
    <svg class="gear" width="18" height="18" viewBox="0 0 18 18"><circle cx="7" cy="10" r="4.5" fill="none" stroke="#333" stroke-width="3" stroke-dasharray="2 1.5"/><circle cx="14" cy="4" r="2.5" fill="none" stroke="#333" stroke-width="1.8"/></svg>
    <span class="brand"><span class="brand-dot"></span>Zenqo</span>
  </div>
  <header class="header header--balance">
    <div class="back-block"></div>
    <span class="back-link">‹ Indietro</span>
    <div class="balance-label">Il Tuo Saldo</div>
    <div class="balance-value">€106.82</div>
    <div class="avatar" role="img" aria-label="User profile photo"></div>
  </header>
  <div class="range-select"><span>Ultimi 30 Giorni</span><span>⌄</span></div>
  <ul class="transactions">
    <li class="transaction"><span class="kind"><svg width="12" height="10" viewBox="0 0 12 10"><path d="M6 0l6 5h-2v5H7V7H5v3H2V5H0z" fill="#fff"/></svg></span><span class="number">+39 351 604 8837</span><span class="sum">€ 1</span><span class="more">▶</span></li>
    <li class="transaction"><span class="kind"><svg width="12" height="10" viewBox="0 0 12 10"><path d="M6 0l6 5h-2v5H7V7H5v3H2V5H0z" fill="#fff"/></svg></span><span class="number">+39 351 604 8837</span><span class="sum">€ -1</span><span class="more">▶</span></li>
    <li class="transaction"><span class="kind"><svg width="12" height="10" viewBox="0 0 12 10"><path d="M6 0l6 5h-2v5H7V7H5v3H2V5H0z" fill="#fff"/></svg></span><span class="number">+39 004 917 3360</span><span class="sum">€ 200</span><span class="more">▶</span></li>
    <li class="transaction"><span class="kind"><svg width="12" height="10" viewBox="0 0 12 10"><path d="M6 0l6 5h-2v5H7V7H5v3H2V5H0z" fill="#fff"/></svg></span><span class="number">+39 575 282 9014</span><span class="sum">€ 12</span><span class="more">▶</span></li>
    <li class="transaction"><span class="kind"><svg width="12" height="10" viewBox="0 0 12 10"><path d="M6 0l6 5h-2v5H7V7H5v3H2V5H0z" fill="#fff"/></svg></span><span class="number">+39 351 604 8837</span><span class="sum">€ -1</span><span class="more">▶</span></li>
    <li class="transaction"><span class="kind"><svg width="12" height="10" viewBox="0 0 12 10"><path d="M6 0l6 5h-2v5H7V7H5v3H2V5H0z" fill="#fff"/></svg></span><span class="number">+39 004 917 3360</span><span class="sum">€ 200</span><span class="more">▶</span></li>
    <li class="transaction"><span class="kind"><svg width="12" height="10" viewBox="0 0 12 10"><path d="M6 0l6 5h-2v5H7V7H5v3H2V5H0z" fill="#fff"/></svg></span><span class="number">+39 575 282 9014</span><span class="sum">€ 12</span><span class="more">▶</span></li>
  </ul>
  <div class="actions">
    <span class="action action--report">Report</span>
    <span class="action action--pockets">Tasche</span>
  </div>
</section>

</body>
</html>
```